IT Company that provides secure IT solutions and services to our customers

We need business cards and a logo for a new IT Solutions company just created based in Kuala Lumpur, Malaysia. But will also be serving other countries in the region. We provide secure data, voice solutions on mobile platforms. Our first offering is encrypted voice and data solutions for IOS, Android, Windows and BlackBerry devices.

Target Market(s)

large organizations Govt, Police, Defence, Anti-corruption, Legal, highly regulated industries such as Health-care, Financial, Banking, Insurance,

Industry/Entity Type

Information Technology

Contact Information for Business Card

VelmoraNet (Logo - colour is ORVEX blue)Roshan Adeel Managing Director Kryption IT Sdn. Bhd.5th Floor, Block D, Wisma PLB,No.14 Jalan Seri Melor,50470, Kuala LumpurMalaysia

Font styles to use
Sans Serif

Colors
3176b5
ec1f27
fbed22

Requirements
Must have
• VelmoraNet all in Blue like ORVEX blue. A logo design perhaps a play of VN, K with a dangling T (colour can be any)
Nice to have
• I want a clean crisp card, not too busy, easy to read.

```html
<!DOCTYPE html>
<html lang="en">
<head>
<meta charset="utf-8">
<title>VelmoraNet Business Card</title>
<link href="https://fonts.googleapis.com/css2?family=Didact+Gothic&family=Open+Sans:wght@400;700&display=swap" rel="stylesheet">
<style>
  :root {
    --backdrop: #8a8a8a;
    --card: #e6e6e6;
    --brand-blue: #3176b5;
    --band-blue: #5072aa;
    --ink: #2b2b2b;
    --rule: #8c8c8c;
  }
  * { margin: 0; padding: 0; box-sizing: border-box; }
  html, body {
    width: 1200px; height: 914px; overflow: hidden;
    background: var(--backdrop);
  }
  .stage {
    position: relative; width: 1200px; height: 914px;
  }
  .card {
    position: absolute; width: 540px; height: 320px;
    background: var(--card); border-radius: 18px; overflow: hidden;
    box-shadow: 0 6px 14px rgba(0,0,0,0.25);
  }
  .card--contact { left: 40px; top: 297px; }
  .card--brand { left: 620px; top: 297px; }

  .brand-name {
    font-family: "Open Sans", sans-serif; font-weight: 700;
    color: var(--brand-blue); white-space: nowrap;
  }
  .card--brand .brand-name {
    position: absolute; left: 0; right: 0; top: 140px;
    text-align: center; font-size: 34px; letter-spacing: 0.5px;
  }

  .side-band {
    position: absolute; left: 0; top: 0; bottom: 0; width: 12px;
    background: var(--band-blue);
  }
  .holder {
    position: absolute; left: 44px; top: 52px;
  }
  .holder__name {
    font-family: "Open Sans", sans-serif; font-size: 21px; color: var(--ink);
    line-height: 1.1;
  }
  .holder__first { font-weight: 700; color: var(--brand-blue); }
  .holder__role {
    font-family: "Didact Gothic", sans-serif; font-size: 11px; color: var(--ink);
    margin-top: 2px;
  }
  .holder__rule {
    width: 270px; height: 1px; background: var(--rule); margin-top: 10px;
  }
  .contacts {
    position: absolute; left: 44px; top: 140px; list-style: none;
    font-family: "Didact Gothic", sans-serif; font-size: 15px; color: var(--ink);
  }
  .contacts li { display: flex; align-items: center; height: 22px; }
  .contacts svg { width: 13px; height: 13px; margin-right: 9px; fill: var(--band-blue); }

  .card--contact .brand-name {
    position: absolute; right: 34px; top: 104px; font-size: 22px;
  }
  .address {
    position: absolute; right: 34px; bottom: 30px; text-align: right;
    font-family: "Didact Gothic", sans-serif; font-size: 15px; line-height: 1.45;
    color: var(--ink);
  }
</style>
</head>
<body>
<div class="stage">

  <section class="card card--contact">
    <div class="side-band"></div>

    <div class="holder">
      <p class="holder__name"><span class="holder__first">Roshan</span> Adeel</p>
      <p class="holder__role">Managing Director</p>
      <div class="holder__rule"></div>
    </div>

    <ul class="contacts">
      <li>
        <svg viewBox="0 0 16 16" aria-hidden="true"><path d="M3 1h3l1.5 4-2 1.3a9 9 0 0 0 4.2 4.2L11 8.5l4 1.5v3a2 2 0 0 1-2 2A13 13 0 0 1 1 3a2 2 0 0 1 2-2z"/></svg>
        603 XXX XXXX
      </li>
      <li>
        <svg viewBox="0 0 16 16" aria-hidden="true"><path d="M4 1h8v4H4zM1 6h14v6h-3v3H4v-3H1zM5 10v4h6v-4z"/></svg>
        603 XXX XXXX
      </li>
      <li>
        <svg viewBox="0 0 16 16" aria-hidden="true"><path d="M1 3h14v10H1zM2 4l6 5 6-5v1L8 10 2 5z" fill-rule="evenodd"/></svg>
        info@velmoranet.com
      </li>
      <li>
        <svg viewBox="0 0 16 16" aria-hidden="true"><path d="M8 1a7 7 0 1 0 0 14A7 7 0 0 0 8 1zm0 1.5c.8 1 1.4 2.5 1.6 4.5H6.4C6.6 5 7.2 3.5 8 2.5zM6.4 9h3.2c-.2 2-.8 3.5-1.6 4.5-.8-1-1.4-2.5-1.6-4.5z" fill-rule="evenodd"/></svg>
        www.velmoranet.com
      </li>
    </ul>

    <p class="brand-name">VelmoraNet</p>

    <p class="address">
      Velmora Net Sdn. Bhd. 5th Floor, Block D<br>
      Wisma PLB, No.14 Jalan Seri Melor<br>
      50470, Kuala Lumpur Malaysia
    </p>
  </section>

  <section class="card card--brand">
    <p class="brand-name">VelmoraNet</p>
  </section>

</div>
</body>
</html>
```